Business card design for Virtual Assistance company

I need a business card designed for my virtual assistance company. We are a small company who services primarily C-level executive clients. The card needs to be double sided with the following contact information on the back:
Melissa Thornbury
Owner/CEO
info@rkpadvisory.net
www.rkpadvisory.net
555.302.9817

The front side should just have the company name incorporated: "RKP Advisory" and "virtual assistance"

The card should be simplistic, but eye catching and should speak to high level executives. Our primary focus areas consist of executive assistance and government contracting.

Target Market(s)

CEOs and executives

Contact Information for Business Card

see project description. phone, email, website.

Colors

Designer to choose only greyscale colors for use in the design.

```html
<!DOCTYPE html>
<html lang="en">
<head>
<meta charset="utf-8">
<title>RKP Advisory – Business Card</title>
<link rel="stylesheet" href="https://fonts.googleapis.com/css2?family=EB+Garamond:wght@400;600;700&family=Montserrat:wght@400&display=swap">
<style>
  :root {
    --page: #d9d9d9;
    --card: #1b1b1c;
    --card-edge: #111112;
    --ink-white: #f4f4f4;
    --ink-soft: #e2e2e2;
    --ink-mono: #2c2c2e;
    --pattern-light: #3a3a3c;
    --pattern-dark: #141415;
  }
  html, body {
    margin: 0;
    width: 900px;
    height: 1200px;
    overflow: hidden;
    background: var(--page);
  }
  .canvas {
    position: relative;
    width: 900px;
    height: 1200px;
  }
  .card {
    position: absolute;
    left: 80px;
    width: 742px;
    height: 442px;
    border-radius: 24px;
    background: var(--card);
    box-shadow: 0 6px 18px rgba(0,0,0,0.35);
    overflow: hidden;
  }
  .card--front { top: 130px; }
  .card--back { top: 638px; height: 440px; }

  .brand-name {
    position: absolute;
    left: 34px;
    top: 36px;
    margin: 0;
    font-family: "EB Garamond", serif;
    font-weight: 600;
    font-size: 50px;
    line-height: 1;
    color: var(--ink-white);
  }
  .person {
    position: absolute;
    right: 52px;
    top: 48px;
    text-align: right;
  }
  .person__name {
    margin: 0;
    font-family: "EB Garamond", serif;
    font-weight: 700;
    font-size: 27px;
    line-height: 1.05;
    color: var(--ink-white);
  }
  .person__title {
    margin: 2px 0 0;
    font-family: "Montserrat", sans-serif;
    font-size: 15px;
    color: var(--ink-soft);
  }
  .contacts {
    position: absolute;
    left: 44px;
    top: 290px;
    margin: 0;
    padding: 0;
    list-style: none;
    font-family: "Montserrat", sans-serif;
    font-size: 16px;
    color: var(--ink-white);
  }
  .contacts li {
    display: flex;
    align-items: center;
    height: 28px;
  }
  .contacts svg {
    width: 16px;
    height: 16px;
    margin-right: 9px;
    fill: var(--ink-white);
  }
  .tagline {
    position: absolute;
    left: 44px;
    top: 390px;
    margin: 0;
    font-family: "EB Garamond", serif;
    font-size: 18px;
    letter-spacing: 0.3px;
    color: var(--ink-soft);
  }
  .brand-mark-large {
    position: absolute;
    right: 44px;
    bottom: 44px;
    margin: 0;
    font-family: "EB Garamond", serif;
    font-weight: 600;
    font-size: 58px;
    line-height: 1;
    color: var(--ink-mono);
  }
  .pattern-field {
    position: absolute;
    inset: 0;
    background: linear-gradient(100deg, var(--pattern-light) 0%, #262628 35%, var(--pattern-dark) 60%, #1c1c1d 100%);
  }
  .brand-mark-small {
    position: absolute;
    right: 86px;
    top: 258px;
    margin: 0;
    font-family: "EB Garamond", serif;
    font-weight: 600;
    font-size: 34px;
    line-height: 1;
    color: var(--ink-white);
  }
</style>
</head>
<body>
<main class="canvas">

  <section class="card card--front" aria-label="Card front">
    <h1 class="brand-name">RKP Advisory</h1>
    <div class="person">
      <p class="person__name">Melissa Thornbury</p>
      <p class="person__title">Owner/CEO</p>
    </div>
    <ul class="contacts">
      <li>
        <svg viewBox="0 0 16 16" aria-hidden="true"><path d="M3.2 1.5l2.3 2.6-1.2 1.6c.9 2 2.3 3.4 4.2 4.4l1.6-1.2 2.6 2.3-1.1 2.3C6.3 13.2 2.8 9.6 1 4.3z"/></svg>
        555.302.9817
      </li>
      <li>
        <svg viewBox="0 0 16 16" aria-hidden="true"><path d="M1.5 3.5h13v1.2L8 9 1.5 4.7z"/><path d="M1.5 6.3L8 10.6l6.5-4.3v6.2h-13z"/></svg>
        info@rkpadvisory.net
      </li>
      <li>
        <svg viewBox="0 0 16 16" aria-hidden="true"><circle cx="8" cy="8" r="6.5"/><path d="M5 4.5l2 1-1 2 2 1-1 3-2-2zM10 3.5l2 2-2 1z" fill="#1b1b1c"/></svg>
        www.rkpadvisory.net
      </li>
    </ul>
    <p class="tagline">VIRTUAL ASSISTANCE</p>
    <p class="brand-mark-large">RKP Advisory</p>
  </section>

  <section class="card card--back" aria-label="Card back">
    <div class="pattern-field" role="img" aria-label="Repeating embossed monogram pattern in graded greys"></div>
    <p class="brand-mark-small">RKP Advisory</p>
  </section>

</main>
</body>
</html>
```